Calder Vane LED - E- Commerce site

We need a website designed for an LED Billboard company that sells:
1) LED Billboards (Sales & Rental)
2) LED Gas Station lights
3) Truss Systems (Sales & Rental)
4) Sound Systems (Sales & Rental)

Attached are websites that sell similar products as Calder Vane LED. Target market is for business, property managers and event coordinators.
This site will need to be an e-commerce site where customers can purchase the product directly from the site. What I'm looking for is a design layout to start.

Conceptual Web Designs:
http://192.0.2.47:8087/index.html
http://www.pmvdisplay.example/
http://www.auralomaaudio.example/
http://www.quillmarkpanel.example/

Attached is the logo of the company: Please note that the new spelling of the logo is "Calder Vane LED" using domain " CalderVaneLED.com

Industry/Entity Type

Gas Station

Number of Pages Required

5+ page

Requirements
Must have
• 1) E-Commerce - Customers will need to be able to order product from the site.
• 2) Customers will also have the option to rent the product as well.
Nice to have
• I like the image of the attached website, that has a video clip loop
• http://www.quillmarkpanel.example/

```html
<!DOCTYPE html>
<html lang="en">
<head>
<meta charset="utf-8">
<title>Calder Vane LED</title>
<link rel="stylesheet" href="https://fonts.googleapis.com/css2?family=Audiowide&family=Open+Sans:wght@400;600;700&display=swap">
<style>
:root{
  --yellow:#f0b619;
  --yellow-dark:#d99e08;
  --black:#111111;
  --ink:#333333;
  --muted:#8a8a8a;
  --line:#dddddd;
  --panel:#f0f0f0;
  --white:#ffffff;
  --tech:#f0b619;
  --price:#5bb347;
  --service:#e52b2b;
  --quality:#1ea6b8;
  --warranty:#9b2a8c;
}
*{box-sizing:border-box;margin:0;padding:0}
html,body{width:1200px;height:2703px;overflow:hidden}
body{font-family:"Open Sans",Arial,sans-serif;color:var(--ink);background:var(--white);position:relative}
.display{font-family:"Audiowide","Open Sans",sans-serif}
a{color:inherit;text-decoration:none}

/* header */
.topbar{position:absolute;left:0;top:0;width:1200px;height:101px;background:var(--black);color:var(--white)}
.brand{position:absolute;left:162px;top:30px;display:flex;align-items:center;gap:12px}
.brand-dot{width:40px;height:40px;border-radius:50%;background:var(--yellow)}
.brand-name{font-family:"Audiowide",sans-serif;font-size:24px;color:var(--white)}
.utility{position:absolute;right:162px;top:14px;display:flex;gap:26px;font-size:11px;align-items:center}
.utility .phone{font-size:14px}
.utility .phone b{font-weight:700}
.search{position:absolute;left:667px;top:54px;width:230px;height:29px;display:flex}
.search span{flex:1;background:var(--white);color:#999;font-size:10px;padding:8px 10px}
.search i{width:29px;background:var(--yellow);display:flex;align-items:center;justify-content:center}
.cart{position:absolute;left:920px;top:52px;display:flex;gap:8px;font-size:10px;line-height:14px}
.cart i{width:30px;height:30px;border-radius:50%;background:var(--yellow);display:flex;align-items:center;justify-content:center}

.nav{position:absolute;left:0;top:101px;width:1200px;height:50px;background:linear-gradient(#fafafa,#dedede);display:flex;padding-left:162px}
.nav a{font-family:"Audiowide",sans-serif;font-size:12.5px;color:#222;padding:0 24px;line-height:50px}
.nav a.active{background:var(--yellow);color:var(--white);padding:0 30px}

/* hero */
.hero{position:absolute;left:0;top:151px;width:1200px;height:462px;background:linear-gradient(160deg,#4d5a1a 0%,#2b3412 40%,#6b4a16 75%,#1d1a10 100%)}
.hero-title{position:absolute;width:100%;top:240px;text-align:center;color:var(--white);font-family:"Audiowide",sans-serif;line-height:46px}
.hero-title .l1{font-size:44px;letter-spacing:2px}
.hero-title .l2{font-size:36px;letter-spacing:2px}
.hero .play{position:absolute;left:564px;top:148px}
.hero .arrow{position:absolute;top:364px}

/* sections */
.section-title{position:absolute;width:100%;text-align:center;font-family:"Audiowide",sans-serif;font-size:24px;color:#555;display:flex;justify-content:center;align-items:center;gap:10px}
.section-title .mark{width:30px;height:30px;border-radius:50%;border:4px solid var(--yellow)}
.section-title em{font-style:normal;color:var(--yellow)}
.tabs{position:absolute;display:flex;gap:10px}
.tab{font-family:"Audiowide",sans-serif;font-size:14px;height:36px;line-height:34px;padding:0 18px;border:2px solid var(--line);color:#999;background:var(--white);position:relative}
.tab.on{background:var(--yellow);border-color:var(--yellow);color:var(--white)}
.tab.on:after{content:"";position:absolute;left:50%;bottom:-9px;margin-left:-8px;border:8px solid transparent;border-top-color:var(--yellow);border-bottom:0}

.welcome{position:absolute;left:0;top:613px;width:1200px;height:454px;background:var(--white)}
.service{position:absolute;top:135px;width:202px}
.service .photo{height:147px}
.service h3{font-family:"Audiowide",sans-serif;font-size:15px;color:#222;margin-top:18px;line-height:20px;min-height:20px}
.service p{font-size:10.5px;color:#777;line-height:18px;margin-top:6px;height:44px}
.btn-more{display:inline-block;margin-top:14px;background:var(--yellow);color:var(--white);font-family:"Audiowide",sans-serif;font-size:11px;padding:7px 14px}

.new{position:absolute;left:0;top:1067px;width:1200px;height:450px;background:var(--panel)}
.product{position:absolute;width:206px;height:300px;background:var(--white);text-align:center;padding:7px;box-shadow:0 0 0 1px #e4e4e4}
.product .photo{height:142px;background:#f3f3f3}
.product .price{font-size:14px;font-weight:700;color:var(--yellow);margin-top:20px}
.product h4{font-family:"Audiowide",sans-serif;font-size:12px;color:#333;margin-top:8px}
.product p{font-size:10px;color:#999;line-height:15px;margin-top:8px}
.product .actions{display:flex;justify-content:center;gap:8px;margin-top:26px}
.product .actions i{width:28px;height:28px;border-radius:50%;border:2px solid #ccc;display:flex;align-items:center;justify-content:center}
.product .actions i.cartbtn{background:var(--yellow);border-color:var(--yellow)}
.product.featured{background:var(--yellow)}
.product.featured .photo{background:var(--white)}
.product.featured .price,.product.featured h4,.product.featured p{color:var(--white)}
.product.featured .actions i{border-color:var(--white);background:transparent}

.why{position:absolute;left:0;top:1517px;width:1200px;height:357px;background:var(--white)}
.reason{position:absolute;top:100px;width:170px;text-align:center}
.reason .badge{width:88px;height:88px;border-radius:50%;margin:0 auto;border:4px solid var(--white);display:flex;align-items:center;justify-content:center}
.reason h5{font-family:"Audiowide",sans-serif;font-size:14px;font-weight:400;color:#333;margin-top:26px;letter-spacing:1px}
.reason p{font-size:10.5px;color:#777;line-height:20px;margin-top:10px}

.catalog{position:absolute;left:0;top:1874px;width:1200px;height:515px;background:linear-gradient(#f1f2f4,#eceded 60%,#f6f6f6)}
.catalog .product{height:308px}

/* footer */
.footer{position:absolute;left:0;top:2389px;width:1200px;height:252px;background:var(--black);color:var(--white)}
.fcol{position:absolute;top:32px}
.fcol h6{font-size:12px;font-weight:700;letter-spacing:.5px;margin-bottom:12px}
.fcol li{list-style:none;font-size:10px;line-height:19px;color:#ddd}
.foot-brand{display:flex;align-items:center;gap:8px;margin-bottom:20px}
.foot-brand span{width:22px;height:22px;border-radius:50%;background:#777}
.foot-brand b{font-family:"Audiowide",sans-serif;font-weight:400;font-size:15px;color:#999}
.newsletter{display:flex;margin-top:14px}
.newsletter span{width:181px;height:30px;background:var(--white);color:#999;font-size:10px;padding:9px 10px}
.newsletter b{width:81px;height:30px;background:var(--yellow);font-family:"Audiowide",sans-serif;font-size:12px;font-weight:400;line-height:30px;text-align:center}
.social{display:flex;gap:8px;margin-top:10px}
.social i{width:26px;height:26px;border-radius:50%;border:1.5px solid var(--white)}
.bottombar{position:absolute;left:0;top:2641px;width:1200px;height:62px;background:var(--yellow);font-size:10px;color:#333}
.bottombar .links{position:absolute;left:166px;top:24px;display:flex;gap:22px}
.bottombar .copy{position:absolute;right:162px;top:24px}
</style>
</head>
<body>

<header class="topbar">
  <div class="brand"><span class="brand-dot"></span><span class="brand-name">Calder Vane LED</span></div>
  <div class="utility">
    <span class="phone">&#9742; Phone: <b>0400 555 182</b></span>
    <span>&#128100; Create Account</span>
    <span>Login &#9662;</span>
    <span>$ USD &#9662;</span>
    <span>English &#9662;</span>
  </div>
  <div class="search"><span>Enter a keyword...</span><i><svg width="12" height="12" viewBox="0 0 12 12"><circle cx="5" cy="5" r="3.5" fill="none" stroke="#fff" stroke-width="1.6"/><line x1="7.6" y1="7.6" x2="11" y2="11" stroke="#fff" stroke-width="1.6"/></svg></i></div>
  <div class="cart"><i><svg width="14" height="12" viewBox="0 0 14 12"><path d="M1 1h2l2 7h7l1.5-5H4" fill="none" stroke="#fff" stroke-width="1.5"/><circle cx="6" cy="10.5" r="1.2" fill="#fff"/><circle cx="11" cy="10.5" r="1.2" fill="#fff"/></svg></i><span>SHOPPING CART<br>Items (0) - $0.00</span></div>
</header>

<nav class="nav">
  <a class="active" href="#">HOME</a><a href="#">ABOUT</a><a href="#">OUR PRODUCTS</a><a href="#">LED DISPLAYS</a><a href="#">SOLUTION</a><a href="#">GALLERY</a><a href="#">CONTACT</a>
</nav>

<section class="hero" role="img" aria-label="Looping video of a city square lined with illuminated LED billboards at night">
  <svg class="play" width="72" height="72" viewBox="0 0 72 72"><circle cx="36" cy="36" r="33" fill="rgba(0,0,0,.25)" stroke="#fff" stroke-width="4"/><path d="M28 22 L52 36 L28 50Z" fill="#fff"/></svg>
  <div class="hero-title"><div class="l1">WE ARE AN LED</div><div class="l2">BILLBOARD COMPANY</div></div>
  <svg class="arrow" style="left:40px" width="34" height="34" viewBox="0 0 34 34"><circle cx="17" cy="17" r="15" fill="none" stroke="#fff" stroke-width="2"/><path d="M19 11l-6 6 6 6" fill="none" stroke="#fff" stroke-width="2"/></svg>
  <svg class="arrow" style="left:1118px" width="34" height="34" viewBox="0 0 34 34"><circle cx="17" cy="17" r="15" fill="none" stroke="#fff" stroke-width="2"/><path d="M15 11l6 6-6 6" fill="none" stroke="#fff" stroke-width="2"/></svg>
</section>

<section class="welcome">
  <h2 class="section-title" style="top:28px"><span class="mark"></span>WELCOME TO CALDER VANE <em>LED</em></h2>
  <div class="tabs" style="left:492px;top:77px"><span class="tab on" style="width:103px;text-align:center">SALES</span><span class="tab" style="width:105px;text-align:center">RENTAL</span></div>

  <article class="service" style="left:162px"><div class="photo" role="img" aria-label="Red LED sale sign in a shop window" style="background:linear-gradient(135deg,#3a1a1e,#9a2630 55%,#2a1215)"></div><h3>LED BILLBOARDS</h3><p>Sd ut perspiciatis unde omnis isteisteus errorlo sit voluptatem accusantium dolor em que lisS ut persciatis unde omnis.</p><a class="btn-more" href="#">MORE &#10148;</a></article>
  <article class="service" style="left:387px"><div class="photo" role="img" aria-label="Gas station canopy lit at night" style="background:linear-gradient(180deg,#0d2a5a,#2a4f8a 55%,#c9d4e8)"></div><h3>LED GAS<br>STATION LIGHTS</h3><p style="margin-top:6px">Sd ut perspiciatis unde omnis isteisteus errorlo sit voluptatem accusantium.</p><a class="btn-more" href="#" style="margin-top:0">MORE &#10148;</a></article>
  <article class="service" style="left:611px"><div class="photo" role="img" aria-label="Stage truss rig with spotlights" style="background:linear-gradient(180deg,#6a87b8,#a9bedc 60%,#d0dbe9)"></div><h3>TRUSS SYSTEMS</h3><p>Sd ut perspiciatis unde omnis isteisteus errorlo sit voluptatem accusantium dolor em que lisS ut persciatis unde omnis.</p><a class="btn-more" href="#">MORE &#10148;</a></article>
  <article class="service" style="left:834px"><div class="photo" role="img" aria-label="LED spot bulbs on grass" style="background:linear-gradient(180deg,#6f8fa8,#b7c3cc 55%,#5f8a3a)"></div><h3>SOUND SYSTEMS</h3><p>Sd ut perspiciatis unde omnis isteisteus errorlo sit voluptatem accusantium dolor em que lisS ut persciatis unde omnis.</p><a class="btn-more" href="#">MORE &#10148;</a></article>
</section>

<section class="new">
  <h2 class="section-title" style="top:30px"><span class="mark"></span>NEW PRODUCTS</h2>
  <article class="product featured" style="left:162px;top:90px"><div class="photo" role="img" aria-label="Twin-panel LED floodlight"></div><div class="price">$200.00</div><h4>PRODUCT NAME</h4><p>Sed ut perspiciatis unde oml<br>atus error sit voluptatem</p><div class="actions"><i class="cartbtn">&#8203;</i><i></i><i></i></div></article>
  <article class="product" style="left:386px;top:90px"><div class="photo" role="img" aria-label="Black LED floodlight"></div><div class="price">$200.00</div><h4>PRODUCT NAME</h4><p>Sed ut perspiciatis unde oml<br>atus error sit voluptatem</p><div class="actions"><i class="cartbtn"></i><i></i><i></i></div></article>
  <article class="product" style="left:607px;top:90px"><div class="photo" role="img" aria-label="LED tube lights"></div><div class="price">$200.00</div><h4>PRODUCT NAME</h4><p>Sed ut perspiciatis unde oml<br>atus error sit voluptatem</p><div class="actions"><i class="cartbtn"></i><i></i><i></i></div></article>
  <article class="product" style="left:830px;top:90px"><div class="photo" role="img" aria-label="LED cluster bulb"></div><div class="price">$200.00</div><h4>PRODUCT NAME</h4><p>Sed ut perspiciatis unde oml<br>atus error sit voluptatem</p><div class="actions"><i class="cartbtn"></i><i></i><i></i></div></article>
</section>

<section class="why">
  <h2 class="section-title" style="top:32px"><span class="mark"></span>WHY CHOOSE CALDER VANE <em>LED</em></h2>
  <div class="reason" style="left:153px"><div class="badge" style="background:var(--tech);box-shadow:0 0 0 3px var(--tech)"><svg width="34" height="40" viewBox="0 0 34 40"><path d="M17 3a12 12 0 0 0-7 22v5h14v-5A12 12 0 0 0 17 3z" fill="none" stroke="#fff" stroke-width="3"/><line x1="11" y1="35" x2="23" y2="35" stroke="#fff" stroke-width="3"/></svg></div><h5>TECHNOLOGY</h5><p>Sd ut perspiciatis unde is tenatus error sit volu pt at dol oremque lisS ut persciatis ude omnis isteiste natus.</p></div>
  <div class="reason" style="left:333px"><div class="badge" style="background:var(--price);box-shadow:0 0 0 3px var(--price)"><svg width="36" height="36" viewBox="0 0 36 36"><path d="M4 4h14l15 15-14 14L4 18z" fill="#fff"/><circle cx="11" cy="11" r="3" fill="var(--price)"/></svg></div><h5>PRICE</h5><p>Sd ut perspiciatis unde is tenatus error sit volu pt at dol oremque lisS ut persciatis ude omnis isteiste natus.</p></div>
  <div class="reason" style="left:515px"><div class="badge" style="background:var(--service);box-shadow:0 0 0 3px var(--service)"><svg width="36" height="36" viewBox="0 0 36 36"><circle cx="18" cy="18" r="11" fill="none" stroke="#fff" stroke-width="6" stroke-dasharray="4.3 2.6"/><circle cx="18" cy="18" r="8" fill="#fff"/><circle cx="18" cy="18" r="3.5" fill="var(--service)"/></svg></div><h5>SERVICE</h5><p>Sd ut perspiciatis unde is tenatus error sit volu pt at dol oremque lisS ut persciatis ude omnis isteiste natus.</p></div>
  <div class="reason" style="left:697px"><div class="badge" style="background:var(--quality);box-shadow:0 0 0 3px var(--quality)"><svg width="34" height="34" viewBox="0 0 34 34"><rect x="3" y="15" width="7" height="16" fill="#fff"/><path d="M12 15l7-12c3 0 4 2 3 6l-1 4h8c2 0 3 2 2 4l-3 12c-1 2-2 2-4 2H12z" fill="#fff"/></svg></div><h5>QUALITY</h5><p>Sd ut perspiciatis unde is tenatus error sit volu pt at dol oremque lisS ut persciatis ude omnis isteiste natus.</p></div>
  <div class="reason" style="left:877px"><div class="badge" style="background:var(--warranty);box-shadow:0 0 0 3px var(--warranty)"><svg width="30" height="36" viewBox="0 0 30 36"><path d="M15 2l12 5v10c0 9-6 14-12 17C9 31 3 26 3 17V7z" fill="#fff"/><path d="M15 7v21c-4-2-7-6-7-11V10z" fill="var(--warranty)"/></svg></div><h5>WARRANTY</h5><p>Sd ut perspiciatis unde is tenatus error sit volu pt at dol oremque lisS ut persciatis ude omnis isteiste natus.</p></div>
</section>

<section class="catalog">
  <h2 class="section-title" style="top:30px"><span class="mark"></span>CALDER VANE <em>LED</em> PRODUCTS</h2>
  <div class="tabs" style="left:225px;top:90px"><span class="tab on">LED BILLBOARDS</span><span class="tab">TRUSSES</span><span class="tab">GAS STATION LIGHTS</span><span class="tab">SOUND SYSTEMS</span></div>
  <article class="product" style="left:162px;top:151px"><div class="photo" role="img" aria-label="Pole-mounted LED billboard screen"></div><div class="price">$200.00</div><h4>PRODUCT NAME</h4><p>Sed ut perspiciatis unde oml<br>atus error sit voluptatem</p><div class="actions"><i class="cartbtn"></i><i></i><i></i></div></article>
  <article class="product" style="left:386px;top:151px"><div class="photo" role="img" aria-label="LED spot bulb"></div><div class="price">$200.00</div><h4>PRODUCT NAME</h4><p>Sed ut perspiciatis unde oml<br>atus error sit voluptatem</p><div class="actions"><i class="cartbtn"></i><i></i><i></i></div></article>
  <article class="product" style="left:607px;top:151px"><div class="photo" role="img" aria-label="Blank billboard frame on a stand"></div><div class="price">$200.00</div><h4>PRODUCT NAME</h4><p>Sed ut perspiciatis unde oml<br>atus error sit voluptatem</p><div class="actions"><i class="cartbtn"></i><i></i><i></i></div></article>
  <article class="product" style="left:830px;top:151px"><div class="photo" role="img" aria-label="LED tube light fitting"></div><div class="price">$200.00</div><h4>PRODUCT NAME</h4><p>Sed ut perspiciatis unde oml<br>atus error sit voluptatem</p><div class="actions"><i class="cartbtn"></i><i></i><i></i></div></article>
</section>

<footer class="footer">
  <div class="fcol" style="left:162px;top:40px">
    <div class="foot-brand"><span></span><b>Calder Vane LED</b></div>
    <h6>ABOUT US</h6>
    <ul><li>Company profile</li><li>News</li><li>Certification</li></ul>
  </div>
  <div class="fcol" style="left:364px">
    <h6>LED DISPLAY</h6>
    <ul><li>Traffic Series</li><li>LED Mesh</li><li>Indoor High-Definition Series</li><li>Outdoor Fixed Series</li><li>Rental Indoor Series</li><li>Rental Outdoor Series</li><li>LCD Video Wall series</li><li>Wall Mounted Digital Signage</li><li>Floor Standing LCD Digital</li></ul>
  </div>
  <div class="fcol" style="left:596px">
    <h6>SUPPORT</h6>
    <ul><li>Service Policy</li><li>Download Center</li><li>FAQ</li></ul>
    <h6 style="margin-top:24px">OTHERS</h6>
    <ul><li>Solution</li><li>Gallery</li></ul>
  </div>
  <div class="fcol" style="left:776px">
    <h6 style="margin-bottom:4px">SIGN UP NEWSLETTER</h6>
    <ul><li>Please sign up here for latest deals</li></ul>
    <div class="newsletter"><span>Email address</span><b>SIGN UP</b></div>
    <h6 style="margin-top:28px;margin-bottom:0">FOLLOW US</h6>
    <div class="social"><i></i><i></i><i></i><i></i><i></i></div>
  </div>
</footer>
<div class="bottombar">
  <div class="links"><span>Privacy statement</span><span>Use terms</span><span>Site Map</span></div>
  <div class="copy">Copyright 2016 &copy; CalderVaneLED Ltd. ALL Rights Reserved</div>
</div>

</body>
</html>
```